Business Card Design Project - del varosi group

dear Sirs

we need business card design for our group ( DEL Varosi Group ) , i have got the Logo design of our group from pixel harbor in previous , so all need details relating to our group i think available with you, as well as the the chosen logo design

we hope to provide us with business card logo that to be appropaite and satisfactory to us .

thanks

note : logo design of our group is attached .
Updates

Reason: please extend the deadline of my project for additional 15 days because i didn't received appropriate design for our gruop yet . kindly beaware that i have received 77 design till now , supossed to send me 200-250 design at least . thanks

Target Market(s)

contents

name : Kerem EL Nadiri

position : Operation Manager

Industry/Entity Type

Business

Requirements
Must have

• person name

group logo
Nice to have
• logo color matching with back background

```html
<!DOCTYPE html>
<html lang="en">
<head>
<meta charset="utf-8">
<title>DEL Varosi Group – Business Card</title>
<link rel="stylesheet" href="https://fonts.googleapis.com/css2?family=Tinos:wght@400;700&display=swap">
<style>
  :root {
    --page-bg: #e4e5e8;
    --card-light: #ffffff;
    --card-mid: #f2f2f3;
    --card-shade: #dcdcdf;
    --pattern-tone: rgba(200, 200, 204, 0.35);
    --divider: #a9a9ad;
    --brand-blue: #1f4f9c;
    --name-grey: #5a5a5e;
    --ink: #111111;
    --contact-bar: #7a7a7c;
    --contact-text: #ffffff;
    --brand-faint: #aab2d2;
  }
  * { box-sizing: border-box; margin: 0; padding: 0; }
  html, body {
    width: 1067px;
    height: 1200px;
    overflow: hidden;
    background: var(--page-bg);
    font-family: "Tinos", "Times New Roman", serif;
  }
  .sheet {
    width: 1067px;
    height: 1200px;
    display: flex;
    flex-direction: column;
    align-items: center;
    justify-content: center;
    gap: 70px;
  }
  .card {
    position: relative;
    width: 860px;
    height: 490px;
    background: radial-gradient(ellipse at 60% 40%, var(--card-light) 0%, var(--card-mid) 55%, var(--card-shade) 100%);
    box-shadow: 0 6px 18px rgba(0,0,0,0.18);
    overflow: hidden;
  }
  .card__pattern {
    position: absolute;
    border-radius: 50%;
    background: radial-gradient(ellipse at center, var(--pattern-tone) 0%, rgba(200,200,204,0) 70%);
  }
  .card--front .card__pattern { left: 60px; top: 60px; width: 560px; height: 380px; }
  .card--back .card__pattern { left: 110px; top: 40px; width: 560px; height: 420px; }
  .card__divider {
    position: absolute;
    left: 390px;
    top: 38px;
    width: 2px;
    height: 420px;
    background: var(--divider);
  }
  .brand {
    position: absolute;
    display: flex;
    align-items: center;
    gap: 12px;
    font-weight: 700;
    color: var(--brand-blue);
    white-space: nowrap;
  }
  .brand__mark {
    width: 18px;
    height: 18px;
    background: currentColor;
  }
  .card--front .brand {
    left: 34px;
    top: 204px;
    font-size: 34px;
  }
  .card--back .brand {
    left: 0;
    right: 0;
    top: 200px;
    justify-content: center;
    font-size: 76px;
    color: var(--brand-faint);
    gap: 22px;
  }
  .card--back .brand__mark { width: 34px; height: 34px; }
  .person {
    position: absolute;
    right: 44px;
    top: 66px;
    text-align: right;
  }
  .person__name {
    font-size: 40px;
    font-weight: 700;
    line-height: 1.1;
    color: var(--name-grey);
  }
  .person__surname { color: var(--brand-blue); }
  .person__role {
    font-size: 24px;
    color: var(--ink);
    margin-top: 2px;
  }
  .contacts {
    position: absolute;
    left: 410px;
    top: 250px;
    width: 432px;
    list-style: none;
  }
  .contacts__row {
    height: 35px;
    margin-bottom: 3px;
    padding-left: 8px;
    background: var(--contact-bar);
    color: var(--contact-text);
    font-size: 22px;
    line-height: 35px;
  }
</style>
</head>
<body>
<main class="sheet">

  <section class="card card--front" aria-label="Business card front">
    <div class="card__pattern" role="img" aria-label="Soft decorative swoosh pattern in light grey"></div>
    <div class="card__divider"></div>
    <div class="brand">
      <span class="brand__mark"></span>
      <span class="brand__name">DEL Varosi Group</span>
    </div>
    <div class="person">
      <p class="person__name">Kerem <span class="person__surname">EL Nadiri</span></p>
      <p class="person__role">Operation Manager</p>
    </div>
    <ul class="contacts">
      <li class="contacts__row">Phone: 0123 456 789</li>
      <li class="contacts__row">Fax: 0123 456 789</li>
      <li class="contacts__row">info@yourdomain.com</li>
      <li class="contacts__row">www.yourdomain.com</li>
      <li class="contacts__row">PO. Box: City name, etc.</li>
    </ul>
  </section>

  <section class="card card--back" aria-label="Business card back">
    <div class="card__pattern" role="img" aria-label="Soft decorative swoosh pattern in light grey"></div>
    <div class="brand">
      <span class="brand__mark"></span>
      <span class="brand__name">DEL Varosi Group</span>
    </div>
  </section>

</main>
</body>
</html>
```